Business Card Design

We are a company that provides stump grinding services for residential and commercial clients. Looking for a simple business card design that may have some type of graphic on the card that will tie in with the Tamsen name(Grizzly Bear, Paw Print, etc) . Possibly some foliage wrapping around part of the card? Would like to have a simple design that stands out because it is unique. We are working on getting the website set up and there is a simple graphic on the top of the page that came to mind when I mentioned the leaves.

Industry/Entity Type

Business

Contact Information for Business Card

Tamsen Stump Grinding 303-257-4788KodiakStumps.Com

Font styles to use
Serif

Requirements
Must have
• Business name
• Website Address
• Phone Number
Nice to have
• Graphics that would be associated with a Tamsen bear.
Should not have
• Nothing frilly

```html
<!DOCTYPE html>
<html lang="en">
<head>
<meta charset="utf-8">
<title>Tamsen Stump Grinding – Business Card</title>
<link href="https://fonts.googleapis.com/css2?family=Cinzel:wght@400;600&family=Open+Sans:wght@400&display=swap" rel="stylesheet">
<style>
  :root {
    --backdrop: #2a2a2a;
    --card: #151515;
    --card-edge: #222222;
    --ink: #f2f2f2;
    --ink-muted: #6e6e6e;
    --rule: #3a3a3a;
    --ring: #8a8a8a;
  }
  * { margin: 0; padding: 0; box-sizing: border-box; }
  html, body {
    width: 1200px; height: 900px; overflow: hidden;
    background: var(--backdrop);
  }
  .stage {
    position: relative; width: 1200px; height: 900px;
    display: flex; align-items: center; justify-content: center; gap: 60px;
  }
  .card {
    position: relative;
    width: 510px; height: 300px;
    background: var(--card);
    border: 1px solid var(--card-edge);
    border-radius: 22px;
    box-shadow: 0 14px 30px rgba(0,0,0,0.45);
  }

  /* name placeholder standing where the mark sits */
  .brand-name {
    display: flex; align-items: center; gap: 12px;
    font-family: "Cinzel", serif; font-weight: 400;
    color: var(--ink); white-space: nowrap; line-height: 1;
  }
  .brand-name .dot {
    flex: none; width: 16px; height: 16px; border-radius: 50%;
    background: var(--ring);
  }

  /* back side */
  .card-back .brand-name {
    position: absolute; left: 56px; top: 50%; transform: translateY(-50%);
    font-size: 30px; letter-spacing: 1px;
  }
  .card-back .divider {
    position: absolute; left: 292px; top: 60px; width: 1px; height: 180px;
    background: var(--rule);
  }
  .contact-list {
    position: absolute; left: 318px; top: 96px;
    list-style: none;
    font-family: "Open Sans", sans-serif; font-size: 14px;
    color: var(--ink);
  }
  .contact-list li {
    display: flex; align-items: center; gap: 10px; margin-bottom: 8px;
  }
  .contact-list svg { width: 12px; height: 12px; fill: none; stroke: var(--ink-muted); stroke-width: 2; }

  /* front side */
  .card-front {
    display: flex; flex-direction: column; align-items: center; justify-content: center;
  }
  .card-front .brand-name {
    font-size: 24px; letter-spacing: 1px; margin-bottom: 22px;
  }
  .business-name {
    font-family: "Cinzel", serif; font-weight: 600;
    font-size: 26px; color: var(--ink); letter-spacing: 1px;
    line-height: 1;
  }
  .business-line {
    font-family: "Cinzel", serif; font-weight: 400;
    font-size: 20px; color: var(--ink-muted);
    letter-spacing: 16px; margin-top: 8px; margin-right: -16px;
  }
</style>
</head>
<body>
<main class="stage">
  <section class="card card-back" aria-label="Card back">
    <div class="brand-name">
      <span class="dot"></span>
      <span>Tamsen</span>
    </div>
    <span class="divider"></span>
    <ul class="contact-list">
      <li>
        <svg viewBox="0 0 12 12"><path d="M2 3c0-1 1-1.5 1.5-1.5L5 4 4 5c.5 1.2 1.8 2.5 3 3l1-1 2.5 1.5c0 .5-.5 1.5-1.5 1.5C5 10 2 7 2 3z"/></svg>
        <span>303-555-0146</span>
      </li>
      <li>
        <svg viewBox="0 0 12 12"><path d="M5 7 7 5M4 5 2.5 6.5a2 2 0 0 0 3 3L7 8M8 7l1.5-1.5a2 2 0 0 0-3-3L5 4"/></svg>
        <span>TamsenStumps.Com</span>
      </li>
    </ul>
  </section>

  <section class="card card-front" aria-label="Card front">
    <div class="brand-name">
      <span class="dot"></span>
      <span>Tamsen</span>
    </div>
    <h1 class="business-name">TAMSEN STUMP</h1>
    <p class="business-line">GRINDING</p>
  </section>
</main>
</body>
</html>
```